Insurance Agency website design for Brellow Cover Insurance, LP

Build a website for Brellow Cover Insurance, LP which sells Homeowners, Auto, Renters, Condo, Flood, Disability, Life, Umbrella, and health insurance. We need the coolest insurance agency website out there to get quotes, contact us, or get additional information. Please list the following insurance companies we work with: Varnix, Ostle, Meridale Mutual, Quillor, Dunmarrow, KGZ, and Pellwick.

Make a design similar to https://www.fernagentry.com/

Selling personal insurance policies

```html
<!DOCTYPE html>
<html lang="en">
<head>
<meta charset="utf-8">
<title>Brellow Cover Insurance, LP</title>
<link href="https://fonts.googleapis.com/css2?family=Montserrat:wght@400;500;600;700;800&display=swap" rel="stylesheet">
<style>
:root{
  --green:#0b8a3e;
  --green-dark:#1d5a3a;
  --blue:#1c46c9;
  --blue-deep:#1538a8;
  --ink:#1b1f2a;
  --text:#3d4250;
  --muted:#6b7080;
  --pale:#eef2f8;
  --white:#ffffff;
  --footer:#11151f;
}
*{margin:0;padding:0;box-sizing:border-box}
html,body{width:1200px;height:3316px;overflow:hidden;background:var(--white)}
body{font-family:'Montserrat',sans-serif;color:var(--text);position:relative}
.abs{position:absolute}

/* header */
.site-header{position:absolute;top:0;left:0;width:1200px;height:80px;z-index:3}
.brand{position:absolute;display:flex;align-items:center;gap:10px}
.brand-mark{width:30px;height:30px;background:var(--green);border-radius:4px}
.brand-name{font-weight:700;font-size:20px;line-height:1.05;color:var(--blue)}
.site-header .brand{left:110px;top:20px}
.main-nav{position:absolute;left:560px;top:24px;display:flex;align-items:center;gap:30px;font-size:15px;font-weight:600;color:var(--ink)}
.main-nav .active{color:var(--blue);border-bottom:2px solid var(--blue);padding-bottom:3px}
.btn{display:inline-block;background:var(--green);color:var(--white);font-weight:600;border-radius:22px;font-size:14px;padding:10px 22px}
.agent{position:absolute;left:900px;top:18px;display:flex;align-items:center;gap:10px}
.icon-circle{width:40px;height:40px;border-radius:50%;background:var(--blue);display:flex;align-items:center;justify-content:center}
.agent small{display:block;font-size:11px;color:var(--muted)}
.agent strong{font-size:19px;color:var(--ink);font-weight:700}

/* hero */
.hero{position:absolute;top:0;left:0;width:1200px;height:640px}
.hero-photo{position:absolute;left:520px;top:0;width:680px;height:560px;background:linear-gradient(160deg,#c9d6e6 0%,#dfe6ee 45%,#9fb28a 100%)}
.hero-text{position:absolute;left:120px;top:180px;width:420px;font-size:17px;line-height:1.65;color:var(--text)}
.hero-text b{color:var(--green)}
.slider-dots{position:absolute;left:40px;top:270px;display:flex;flex-direction:column;gap:12px}
.slider-dots span{width:12px;height:12px;border-radius:50%;border:2px solid #9aa2b0}
.slider-dots .on{background:var(--green);border-color:var(--green)}
.inquiry-bar{position:absolute;left:120px;top:545px;width:980px;height:95px;background:var(--green);display:flex;align-items:center;z-index:2}
.inquiry-photo{width:205px;height:95px;background:linear-gradient(135deg,#e8ece8,#b9c4bd)}
.inquiry-label{width:220px;margin-left:25px;color:var(--white);font-weight:700;font-size:20px;line-height:1.3}
.inquiry-contacts{margin-left:60px;color:var(--white);font-size:18px;font-weight:600;display:flex;flex-direction:column;gap:12px}
.inquiry-contacts div{display:flex;align-items:center;gap:14px}
.inquiry-contacts .phone{font-size:24px;font-weight:700}

/* contact */
.contact{position:absolute;top:640px;left:0;width:1200px;height:660px;background:linear-gradient(180deg,var(--blue) 0%,var(--blue-deep) 100%);text-align:center;color:var(--white)}
.eyebrow{font-size:13px;font-weight:500;letter-spacing:1px;text-transform:uppercase}
.section-title{font-size:38px;font-weight:700;line-height:1.2}
.section-title .hl{color:var(--green)}
.contact .eyebrow{margin-top:55px}
.contact p.lead{width:600px;margin:18px auto 0;font-size:17px;line-height:1.5}
.contact-form{position:absolute;left:270px;top:205px;width:660px}
.field{height:40px;background:var(--white);border-radius:3px;margin-bottom:18px;display:flex;align-items:center;gap:12px;padding-left:14px;color:#8a90a0;font-size:13px;text-align:left}
.field.message{height:130px;align-items:flex-start;padding-top:12px}
.send{display:inline-block;margin-top:16px;border:2px solid var(--white);border-radius:22px;padding:10px 30px;font-size:13px;font-weight:600;color:var(--white)}

/* partners */
.partners{position:absolute;top:1300px;left:0;width:1200px;height:320px;background:var(--pale);text-align:center}
.partners .eyebrow{margin-top:85px;color:var(--text)}
.partners .section-title{color:var(--ink)}
.partner-row{position:absolute;left:0;top:200px;width:1200px;display:flex;justify-content:space-around;align-items:center;padding:0 10px}
.partner-row span{font-size:21px;font-weight:700;color:#2c3240}

/* about */
.about{position:absolute;top:1620px;left:0;width:1200px;height:700px;text-align:center}
.about .eyebrow{margin-top:0;color:var(--text)}
.about .section-title{color:var(--ink)}
.about .intro{width:800px;margin:14px auto 0;font-size:16px;line-height:1.6}
.about .intro b{color:var(--green)}
.about-text{position:absolute;left:120px;top:200px;width:410px;text-align:right;font-size:16px;line-height:1.6}
.about-text p+p{margin-top:20px}
.about-text b{color:var(--green)}
.about-photo{position:absolute;left:545px;top:200px;width:435px;height:400px;background:linear-gradient(180deg,#bcd3e8 0%,#d9d2c4 55%,#7fa260 100%)}

/* quote */
.quote{position:absolute;top:2330px;left:120px;width:970px;height:610px;background:var(--green-dark);color:var(--white)}
.quote-badge{position:absolute;left:455px;top:-20px;width:60px;height:60px;border-radius:50%;background:var(--white);border:3px solid var(--green-dark);display:flex;align-items:center;justify-content:center}
.quote-head{position:absolute;top:80px;width:970px;text-align:center}
.quote-photo{position:absolute;left:40px;top:180px;width:420px;height:350px;background:linear-gradient(135deg,#d7dbe0 0%,#a9b3a5 100%)}
.quote-text{position:absolute;left:490px;top:180px;width:440px;font-size:16px;line-height:1.6}
.quote-text p+p{margin-top:20px}

/* footer */
.site-footer{position:absolute;top:2990px;left:0;width:1200px;height:326px}
.skyline{position:absolute;top:0;left:0;width:1200px;height:130px;background:linear-gradient(180deg,#e4e7ec 0%,#2a2f3a 100%)}
.footer-band{position:absolute;top:130px;left:0;width:1200px;height:196px;background:var(--footer);color:var(--white)}
.footer-band .brand{left:120px;top:60px}
.footer-band .brand-name{color:var(--white)}
.footer-agent{position:absolute;left:500px;top:62px;display:flex;align-items:center;gap:12px}
.footer-agent small{display:block;font-size:11px;color:#b7bcc8}
.footer-agent strong{font-size:20px}
.footer-nav{position:absolute;left:850px;top:76px;display:flex;gap:30px;font-size:14px;font-weight:500}
.copyright{position:absolute;top:150px;width:1200px;text-align:center;font-size:11px;color:#a7adba}
</style>
</head>
<body>

<header class="site-header">
  <div class="brand"><span class="brand-mark"></span><span class="brand-name">Brellow Cover<br>Insurance, LP</span></div>
  <nav class="main-nav">
    <span class="active">Home</span>
    <span>About</span>
    <span class="btn">Get A Quote</span>
  </nav>
  <div class="agent">
    <span class="icon-circle"><svg width="18" height="18" viewBox="0 0 24 24"><path fill="#fff" d="M6.6 10.8a15.1 15.1 0 0 0 6.6 6.6l2.2-2.2a1 1 0 0 1 1-.25 11.4 11.4 0 0 0 3.6.57 1 1 0 0 1 1 1V20a1 1 0 0 1-1 1A17 17 0 0 1 3 4a1 1 0 0 1 1-1h3.5a1 1 0 0 1 1 1c0 1.25.2 2.45.57 3.57a1 1 0 0 1-.25 1z"/></svg></span>
    <div><small>Talk to an agent</small><strong>612.555.0173</strong></div>
  </div>
</header>

<section class="hero">
  <div class="hero-photo" role="img" aria-label="Family walking hand in hand in front of their home"></div>
  <div class="slider-dots"><span></span><span class="on"></span><span></span></div>
  <p class="hero-text">At <b>BRELLOW COVER INSURANCE</b>, we understand that your peace of mind is invaluable. Our mission is to protect what matters most to you—your home, your vehicle, your health, and your loved ones. With our comprehensive range of insurance solutions, we are dedicated to safeguarding your assets and providing you with the security you deserve.</p>
  <div class="inquiry-bar">
    <div class="inquiry-photo" role="img" aria-label="Agent working at a laptop"></div>
    <div class="inquiry-label">For inquiries, please contact us at</div>
    <div class="inquiry-contacts">
      <div class="phone"><svg width="22" height="22" viewBox="0 0 24 24"><path fill="#fff" d="M6.6 10.8a15.1 15.1 0 0 0 6.6 6.6l2.2-2.2a1 1 0 0 1 1-.25 11.4 11.4 0 0 0 3.6.57 1 1 0 0 1 1 1V20a1 1 0 0 1-1 1A17 17 0 0 1 3 4a1 1 0 0 1 1-1h3.5a1 1 0 0 1 1 1c0 1.25.2 2.45.57 3.57a1 1 0 0 1-.25 1z"/></svg>612.555.0173</div>
      <div><svg width="22" height="22" viewBox="0 0 24 24"><path fill="none" stroke="#fff" stroke-width="2" d="M3 5h18v14H3zM3 5l9 8 9-8"/></svg>info@BrellowCover.com</div>
    </div>
  </div>
</section>

<section class="contact">
  <div class="eyebrow">Get in touch</div>
  <h2 class="section-title">Contact Us</h2>
  <p class="lead">Protect what matters most. Contact us today for a personalized quote and secure the coverage you need.</p>
  <div class="contact-form">
    <div class="field">&#9786; Your Name</div>
    <div class="field">&#9993; Email</div>
    <div class="field">&#9742; Phone Number</div>
    <div class="field message">&#9998; Write A Message</div>
    <span class="send">SEND MESSAGE</span>
  </div>
</section>

<section class="partners">
  <div class="eyebrow">Our trusted partners</div>
  <h2 class="section-title">Companies We Work With</h2>
  <div class="partner-row">
    <span>Varnix</span><span>Ostle</span><span>Meridale Mutual</span><span>Quillor</span><span>KGZ</span><span>Dunmarrow</span><span>Pellwick</span>
  </div>
</section>

<section class="about">
  <div class="eyebrow">Who we are</div>
  <h2 class="section-title">About <span class="hl">Us</span></h2>
  <p class="intro">Brellow Cover Insurance is a <b>full-service, independent insurance agency</b> with over three decades of experience in delivering comprehensive insurance solutions to individuals.</p>
  <div class="about-text">
    <p>We proudly offer a diverse portfolio of products from more than 20 of the most reputable and financially secure companies in the industry. Our dedicated team of over <b>50 skilled professionals</b> is committed to customizing these products and services to meet the unique needs of each client.</p>
    <p>At Brellow Cover Insurance, our experts are focused on addressing the individual needs of our clients, ensuring <b>exceptional service and support</b> at every step.</p>
  </div>
  <div class="about-photo" role="img" aria-label="Family gathered on the lawn in front of a house"></div>
</section>

<section class="quote">
  <div class="quote-badge"><svg width="26" height="22" viewBox="0 0 26 22"><path fill="#1d5a3a" d="M0 22V12C0 5 3 1 10 0l1 3C7 4 5 7 5 10h5v12zm15 0V12c0-7 3-11 10-12l1 3c-4 1-6 4-6 7h5v12z"/></svg></div>
  <div class="quote-head">
    <div class="eyebrow">Start your quote</div>
    <h2 class="section-title">Get a Quote</h2>
  </div>
  <div class="quote-photo" role="img" aria-label="Couple holding house keys outside their new home"></div>
  <div class="quote-text">
    <p>We believe that securing your home is one of the most important decisions you can make. Obtaining a comprehensive insurance quote is essential to understanding your <b>coverage options and ensuring</b> that your property is adequately protected against unforeseen events.</p>
    <p>Our team of experienced professionals is here to guide you through the process, <b>helping you find the right policy</b> that meets your specific needs and budget. Don't leave your home's safety to chance; get a quote today and take the first step towards peace of mind.</p>
  </div>
</section>

<footer class="site-footer">
  <div class="skyline" role="img" aria-label="City skyline silhouette"></div>
  <div class="footer-band">
    <div class="brand"><span class="brand-mark"></span><span class="brand-name">Brellow Cover<br>Insurance, LP</span></div>
    <div class="footer-agent">
      <span class="icon-circle"><svg width="18" height="18" viewBox="0 0 24 24"><path fill="#fff" d="M6.6 10.8a15.1 15.1 0 0 0 6.6 6.6l2.2-2.2a1 1 0 0 1 1-.25 11.4 11.4 0 0 0 3.6.57 1 1 0 0 1 1 1V20a1 1 0 0 1-1 1A17 17 0 0 1 3 4a1 1 0 0 1 1-1h3.5a1 1 0 0 1 1 1c0 1.25.2 2.45.57 3.57a1 1 0 0 1-.25 1z"/></svg></span>
      <div><small>Talk to an agent</small><strong>612.555.0173</strong></div>
    </div>
    <nav class="footer-nav"><span>Home</span><span>About</span><span>Get a Quote</span></nav>
    <div class="copyright">©2025. All rights reserved.</div>
  </div>
</footer>

</body>
</html>
```